website design for M&T Electric

A portfolio website for a high end commercial and residential electrical contracting company. The current site mandtelectric.example does not represent the current direction but the images in the gallery give you an idea of the work we do. Current logo will be uploaded shortly but is black text on white background.
Target Market(s)
General Contractors, Residential Home Owners, clients intersted in Velmora home automation.
Industry/Entity Type
Electrician
Coding
Coded - Design and coding required
Number of Pages Required
2 page
Font styles to use
Sans Serif
Colors
Designer to choose colors to be used in the design.
Requirements
Must have
- Portfolio section highlighting different service areas and products (Velmora Housepilot, etc)

```html
<!DOCTYPE html>
<html lang="en">
<head>
<meta charset="utf-8">
<title>M&amp;T Electric</title>
<link href="https://fonts.googleapis.com/css2?family=Mulish:wght@300;400;600;700&display=swap" rel="stylesheet">
<style>
:root{
  --orange:#f7931e;
  --orange-deep:#f08a0c;
  --ink:#2b2b2b;
  --muted:#8a8a8a;
  --soft-gray:#e6e6e6;
  --footer:#e9e9e9;
  --green:#5ec41f;
  --white:#ffffff;
  --dark-panel:#2e2b29;
  --night:#1e1a6e;
}
*{box-sizing:border-box;margin:0;padding:0}
html,body{width:1200px;height:2586px;overflow:hidden}
body{font-family:"Mulish",sans-serif;color:var(--ink);background:var(--white);position:relative}
.abs{position:absolute}

/* hero */
.hero{left:0;top:0;width:1200px;height:690px;overflow:hidden;
  background:linear-gradient(160deg,#1b1a8a 0%,#27207a 30%,#1a3a5a 55%,#2c6a3c 75%,#3f2a55 100%)}
.hero-glow{left:560px;top:40px;width:700px;height:560px;
  background:radial-gradient(ellipse at 60% 40%,rgba(90,220,80,.55),rgba(200,60,160,.25) 55%,transparent 75%)}
.hero-city{left:0;top:540px;width:1200px;height:150px;background:linear-gradient(180deg,rgba(20,16,40,0),#1a1420 60%)}
.brand{left:117px;top:36px;font-size:38px;font-weight:400;color:var(--white);letter-spacing:.5px}
.nav{left:495px;top:48px;display:flex;gap:34px;font-size:17px;font-weight:700;color:var(--white)}
.search{left:1044px;top:50px}
.hero-title{left:0;top:278px;width:1200px;text-align:center;font-size:42px;font-weight:600;color:var(--white);letter-spacing:.3px}
.hero-sub{left:0;top:329px;width:1200px;text-align:center;font-size:26.5px;font-weight:700;color:var(--orange);letter-spacing:.3px}
.btn{display:flex;align-items:center;justify-content:center;border-radius:22px;font-size:14px;font-weight:700;color:var(--white);text-transform:uppercase;letter-spacing:.3px}
.btn-orange{background:var(--orange)}
.hero-btn{left:529px;top:383px;width:143px;height:41px}
.dots{left:552px;top:602px;display:flex;gap:10px}
.dots span{width:14px;height:14px;border-radius:50%;background:var(--white)}
.dots span.active{background:transparent;border:2px solid var(--white)}
.hero-curve{left:0;top:590px}

/* services row */
.service{top:715px;width:320px;height:150px}
.service-icon{left:0;top:0;width:98px;height:98px;border-radius:50%;border:1px solid #cfcfcf;background:#fafafa;display:flex;align-items:center;justify-content:center}
.service-title{left:112px;top:0;font-size:24px;line-height:27px;font-weight:400;color:var(--ink)}
.service-text{left:112px;top:60px;width:200px;font-size:12.5px;line-height:18px;color:var(--muted)}
.service-link{left:112px;top:124px;font-size:15px;color:var(--orange-deep)}

/* speciality */
.speciality-bg{left:0;top:919px;width:1200px;height:640px;background:linear-gradient(180deg,var(--soft-gray) 0%,var(--soft-gray) 62%,var(--white) 66%)}
.eyebrow{left:0;top:955px;width:1200px;text-align:center;font-size:18px;color:var(--orange-deep);letter-spacing:.5px}
.section-title{left:0;top:982px;width:1200px;text-align:center;font-size:26px;font-weight:600;letter-spacing:.5px}
.section-lead{left:210px;top:1032px;width:780px;text-align:center;font-size:14.5px;line-height:25px;color:var(--muted)}
.card{top:1117px;width:308px;height:343px;background:var(--white);border:1px solid #d8d8d8;box-shadow:0 1px 3px rgba(0,0,0,.12)}
.card-photo{left:0;top:0;width:306px;height:185px}
.card-title{left:0;top:204px;width:306px;text-align:center;font-size:21px}
.card-text{left:28px;top:242px;width:250px;text-align:center;font-size:13px;line-height:19px;color:var(--muted)}
.card-btn{top:1441px;width:133px;height:38px}

/* about */
.about-panel{left:0;top:1560px;width:600px;height:474px;background:linear-gradient(180deg,#3a3633,var(--dark-panel) 60%,#241f1c)}
.about-photo{left:600px;top:1560px;width:600px;height:474px;background:linear-gradient(180deg,#d8dbe8 0%,#b9bfd6 35%,#6e6a6a 70%,#4a3526 100%)}
.about-title{left:116px;top:1648px;font-size:32px;font-weight:400;color:var(--white)}
.about-text{left:114px;top:1704px;width:425px;font-size:14px;line-height:20.5px;color:#d6d6d6}
.about-text p+p{margin-top:8px}
.about-btn{left:114px;top:1888px;width:136px;height:39px;border:2px solid var(--white);background:transparent}

/* recent work */
.recent-title{left:124px;top:2083px;font-size:31px;font-weight:400}
.work{top:2138px;width:222px;height:237px;background:var(--white);border:4px solid var(--white);box-shadow:0 0 8px rgba(0,0,0,.18)}
.work-photo{left:0;top:0;width:214px;height:174px}
.work-band{left:0;top:174px;width:214px;height:55px;background:var(--green);color:var(--white)}
.work-title{left:18px;top:7px;font-size:19px}
.work-sub{left:18px;top:32px;font-size:10.5px;display:flex;align-items:center;gap:8px}

/* footer */
.footer{left:0;top:2445px;width:1200px;height:141px;background:var(--footer)}
.footer-nav{left:126px;top:42px;display:flex;gap:25px;font-size:17px;color:var(--ink)}
.footer-copy{left:126px;top:79px;font-size:12.5px;color:var(--ink)}
.social{left:925px;top:46px;display:flex;gap:3px}
.social span{width:34px;height:34px;border-radius:50%;border:2px solid var(--ink)}
.footer-mark{left:1158px;top:100px;font-size:12px;color:var(--ink)}
</style>
</head>
<body>

<section class="hero abs">
  <div class="hero-glow abs" role="img" aria-label="Night photograph of a modern building with a glowing green and multicolour lit roof structure"></div>
  <div class="hero-city abs"></div>
  <div class="brand abs">M&amp;T Electric</div>
  <nav class="nav abs"><span>Home</span><span>Gallery</span><span>Speciality Services</span><span>About</span><span>Contact</span></nav>
  <svg class="search abs" width="18" height="18" viewBox="0 0 18 18"><circle cx="7" cy="7" r="5.2" fill="none" stroke="#fff" stroke-width="2.6"/><line x1="11" y1="11" x2="16" y2="16" stroke="#fff" stroke-width="3" stroke-linecap="round"/></svg>
  <h1 class="hero-title abs">COMMECIAL ELECTRICAL SERVICE</h1>
  <div class="hero-sub abs">CURABITUR VEL MISIT AMET MALESUAD</div>
  <div class="btn btn-orange hero-btn abs">Read More</div>
  <div class="dots abs"><span class="active"></span><span></span><span></span><span></span></div>
  <svg class="hero-curve abs" width="1200" height="100" viewBox="0 0 1200 100" preserveAspectRatio="none"><path d="M0 100 L0 95 Q560 20 1200 85 L1200 100 Z" fill="#fff"/></svg>
</section>

<div class="service abs" style="left:117px">
  <div class="service-icon abs">
    <svg width="48" height="60" viewBox="0 0 48 60"><path d="M10 4h28l6 24H4z" fill="#f7931e"/><rect x="22" y="28" width="4" height="24" fill="#f7931e"/><rect x="12" y="52" width="24" height="4" fill="#f7931e"/></svg>
  </div>
  <div class="service-title abs">Residential<br>Services</div>
  <div class="service-text abs">Morbi diam mauris viverra in gravida eu mattis in ante Morbi eget arcu Morbi porta</div>
  <div class="service-link abs">Click here ›</div>
</div>
<div class="service abs" style="left:440px">
  <div class="service-icon abs">
    <svg width="60" height="60" viewBox="0 0 60 60"><path d="M44 10 C54 16 50 32 40 40 L22 52 L10 40 L22 22 C30 12 38 6 44 10Z" fill="none" stroke="#f7931e" stroke-width="2.5"/><path d="M10 40 L4 50 M22 52 L12 56" stroke="#f7931e" stroke-width="2.5"/></svg>
  </div>
  <div class="service-title abs">Commecial<br>Services</div>
  <div class="service-text abs">Morbi diam mauris viverra in gravida eu mattis in ante Morbi eget arcu Morbi porta</div>
  <div class="service-link abs">Click here ›</div>
</div>
<div class="service abs" style="left:772px">
  <div class="service-icon abs">
    <svg width="50" height="56" viewBox="0 0 50 56"><circle cx="25" cy="20" r="16" fill="none" stroke="#f7931e" stroke-width="2.5"/><line x1="25" y1="36" x2="25" y2="52" stroke="#f7931e" stroke-width="2.5"/><line x1="12" y1="52" x2="38" y2="52" stroke="#f7931e" stroke-width="2.5" stroke-linecap="round"/></svg>
  </div>
  <div class="service-title abs">Landscape<br>Services</div>
  <div class="service-text abs">Morbi diam mauris viverra in gravida eu mattis in ante Morbi eget arcu Morbi porta</div>
  <div class="service-link abs">Click here ›</div>
</div>

<section>
  <div class="speciality-bg abs"></div>
  <div class="eyebrow abs">WHAT WE DO</div>
  <h2 class="section-title abs">SPECIALITY SERVICES</h2>
  <p class="section-lead abs">Allamcorper est eget tempor cursus neque mi consectetuer mi a ultricies massa est sed nisl Class aptent taciti sociosqu ad litora torquent per conubia nostra per inceptos hymenaeos Proin nulla arcu</p>

  <div class="card abs" style="left:117px">
    <div class="card-photo abs" role="img" aria-label="Photo of a bronze wall keypad for home automation" style="background:linear-gradient(135deg,#e3b878,#c9945a 60%,#a87240)"></div>
    <div class="card-title abs">Velmora Housepilot</div>
    <div class="card-text abs">Morbi diam mauris viverra in gravida eu mattis in ante Morbi eget arcu Morbi porta libero id ullamcorper</div>
  </div>
  <div class="card abs" style="left:442px">
    <div class="card-photo abs" role="img" aria-label="Photo of glowing LED light bulbs hanging in a row" style="background:radial-gradient(circle at 50% 70%,#fff3d6,#e4a048 35%,#7a3e10 80%)"></div>
    <div class="card-title abs">LED Lighting</div>
    <div class="card-text abs">Morbi diam mauris viverra in gravida eu mattis in ante Morbi eget arcu Morbi porta ullamcorper</div>
  </div>
  <div class="card abs" style="left:771px">
    <div class="card-photo abs" role="img" aria-label="Photo of a standby emergency generator beside a brick house" style="background:linear-gradient(180deg,#9a8a86,#c8c4c0 45%,#8b7f76)"></div>
    <div class="card-title abs">Emergency Generators</div>
    <div class="card-text abs">Morbi diam mauris viverra in gravida eu mattis in ante Morbi eget arcu Morbi porta libero ullamcorper</div>
  </div>
  <div class="btn btn-orange card-btn abs" style="left:201px">Read More</div>
  <div class="btn btn-orange card-btn abs" style="left:530px">Read More</div>
  <div class="btn btn-orange card-btn abs" style="left:864px">Read More</div>
</section>

<section>
  <div class="about-panel abs" role="img" aria-label="Dimmed photo of a dark living room interior"></div>
  <div class="about-photo abs" role="img" aria-label="Photo of a modern living room with blue cove ceiling lighting and a chandelier"></div>
  <h2 class="about-title abs">About M&amp;T Electric</h2>
  <div class="about-text abs">
    <p>Praesent elementum elit at tellus nec ultricies sit amet porttitor mattis enim in massa libero interdum nec interdum vel blandit sed nulla in ullamcorper est</p>
    <p>eget tempor cursus neque mi consectetuer mi a ultricies massa est sed nisl Class aptent taciti sociosqu ad litora torquent per conubia nostra per inceptos hymenaeos Proin nulla arcu nonummy luctus dictum eget fermentum et lorem</p>
  </div>
  <div class="btn about-btn abs">Read More</div>
</section>

<section>
  <h2 class="recent-title abs">Recent Work</h2>
  <div class="work abs" style="left:117px">
    <div class="work-photo abs" role="img" aria-label="Photo of a bright hallway with recessed ceiling lights" style="background:linear-gradient(180deg,#ece6da,#c9bca4 60%,#9c8b70)"></div>
    <div class="work-band abs"><div class="work-title abs">Project Tittle</div><div class="work-sub abs">Donec dictum lectus non odio <svg width="14" height="10" viewBox="0 0 14 10"><path d="M0 5h12M8 1l4 4-4 4" fill="none" stroke="#fff" stroke-width="1.6"/></svg></div></div>
  </div>
  <div class="work abs" style="left:363px">
    <div class="work-photo abs" role="img" aria-label="Photo of a steel roof truss structure with industrial lights" style="background:linear-gradient(180deg,#5a6068,#9aa0a6 50%,#3e4248)"></div>
    <div class="work-band abs"><div class="work-title abs">Project Tittle</div><div class="work-sub abs">Donec dictum lectus non odio <svg width="14" height="10" viewBox="0 0 14 10"><path d="M0 5h12M8 1l4 4-4 4" fill="none" stroke="#fff" stroke-width="1.6"/></svg></div></div>
  </div>
  <div class="work abs" style="left:610px">
    <div class="work-photo abs" role="img" aria-label="Photo of a dining room with a pendant lamp and purple ceiling glow" style="background:linear-gradient(180deg,#6a5aa8,#c9a070 55%,#6a3a1c)"></div>
    <div class="work-band abs"><div class="work-title abs">Project Tittle</div><div class="work-sub abs">Donec dictum lectus non odio <svg width="14" height="10" viewBox="0 0 14 10"><path d="M0 5h12M8 1l4 4-4 4" fill="none" stroke="#fff" stroke-width="1.6"/></svg></div></div>
  </div>
  <div class="work abs" style="left:857px">
    <div class="work-photo abs" role="img" aria-label="Photo of an electrician installing a wall light fixture" style="background:linear-gradient(135deg,#f4e2d6,#d9b29a 55%,#a8755a)"></div>
    <div class="work-band abs"><div class="work-title abs">Project Tittle</div><div class="work-sub abs">Donec dictum lectus non odio <svg width="14" height="10" viewBox="0 0 14 10"><path d="M0 5h12M8 1l4 4-4 4" fill="none" stroke="#fff" stroke-width="1.6"/></svg></div></div>
  </div>
</section>

<footer class="footer abs">
  <nav class="footer-nav abs"><span>Home</span><span>Gallery</span><span>Speciality Services</span><span>About</span><span>Contact</span></nav>
  <div class="footer-copy abs">© 2017 Company Name&nbsp; All right reserved&nbsp; Term of Use</div>
  <div class="social abs" aria-label="Social links"><span></span><span></span><span></span><span></span></div>
  <div class="footer-mark abs">X14</div>
</footer>

</body>
</html>
```